Commercial Refrigeration Service Company requires stylish and fresh looking flyer.

We need a flyer to hand out to new customers. It should have a photo and our branding, list all the services that are offered and our contact details.
We would like two flyers to be supplied, both identical though one offering a discount until July ( Half Price Service Fee ). The flyer should be clear, interesting and in similar colours to the branding package supplied.
Please look at our website for information about the services on offer:
www.brisko-coolworks.com.au

Target Market(s)

Cafes, bars, restaurants, pubs ect.

Font styles to use
Other font styles liked:
• Font package provided

Colors
85cae6
ffffff
333333

Requirements
Must have
• - The photo provided.
• - The company logo.
• - Similar feel to the website & business card.
• - Smooth layout and clear to understand.
Should not have
• - No clunky badges or prints.

```html
<!DOCTYPE html>
<html lang="en">
<head>
<meta charset="utf-8">
<title>Brisko Commercial Refrigeration Flyer</title>
<link rel="stylesheet" href="https://fonts.googleapis.com/css2?family=Questrial&family=Nunito:wght@800&family=Josefin+Sans:wght@300&family=Roboto:wght@700&display=swap">
<style>
:root{
  --ice:#5cc8f0;
  --ice-text:#4fbfe9;
  --ink:#333333;
  --black:#000000;
  --paper-top:#fafafa;
  --paper-bottom:#e4e4e4;
  --icon-grey:#8c8c8c;
  --backdrop:#4a4a4a;
}
*{margin:0;padding:0;box-sizing:border-box}
html,body{width:1200px;height:1146px;overflow:hidden;background:var(--backdrop)}
.flyer{position:absolute;left:223px;top:40px;width:753px;height:1066px;
  background:linear-gradient(180deg,var(--paper-top) 20%,var(--paper-bottom));overflow:hidden;
  font-family:"Questrial",sans-serif;color:var(--ink)}
.header{position:absolute;left:0;top:0;width:100%;height:152px;background:var(--ice)}
.brand-name{position:absolute;top:28px;width:100%;text-align:center;
  font-family:"Josefin Sans",sans-serif;font-weight:300;font-size:50px;letter-spacing:40px;padding-left:40px;color:var(--ink)}
.brand-dot{position:absolute;left:369px;top:100px;width:14px;height:14px;border:1.5px solid var(--ink);border-radius:50%}
.tagline-small{position:absolute;top:168px;width:100%;text-align:center;font-size:11px;letter-spacing:4px}
.tagline-small span{display:inline-block;width:26px;height:1px;background:var(--ink);vertical-align:middle;margin:0 14px}
.tagline-large{position:absolute;top:193px;width:100%;text-align:center;font-size:21px;letter-spacing:9px;padding-left:9px}
.offer{position:absolute;left:125px;top:266px;width:504px;height:113px;border:1px dotted var(--ink);text-align:center;color:var(--ice-text)}
.offer-title{margin-top:16px;font-size:47px;line-height:48px;letter-spacing:-1px}
.offer-sub{font-size:22px;letter-spacing:0}
.services{position:absolute;left:0;top:415px;width:753px;height:370px}
.service{position:absolute;width:200px;text-align:center;white-space:nowrap;font-family:"Nunito",sans-serif;font-weight:800;font-size:20px;line-height:24px;color:var(--ice-text)}
.service-lead{width:400px}
.service svg{display:block;margin:0 auto 12px}
.contact{position:absolute;top:895px;width:100%;text-align:center;font-size:18px;line-height:22px}
.contact .web{font-family:"Roboto",sans-serif;font-weight:700;font-size:17px;letter-spacing:.5px;margin-top:4px}
.bar{position:absolute;top:1025px;height:33px;line-height:33px;font-size:17px;white-space:nowrap}
.bar-phone{left:120px;width:200px;background:var(--black);color:var(--ice);clip-path:polygon(18px 0,100% 0,100% 100%,0 100%);padding-left:34px}
.bar-mail{left:302px;width:333px;background:var(--ice);color:var(--black);clip-path:polygon(0 0,315px 0,100% 100%,0 100%);padding-left:16px}
.bar svg{vertical-align:-2px;margin-right:4px}
.base{position:absolute;top:1058px;left:0;width:100%;height:8px;background:linear-gradient(90deg,var(--black) 40%,var(--ice) 40%)}
</style>
</head>
<body>
<main class="flyer">
  <header class="header">
    <div class="brand-name">BRISKO</div>
    <div class="brand-dot"></div>
  </header>
  <div class="tagline-small"><span></span>COMMERCIAL<span></span></div>
  <div class="tagline-large">REFRIGERATION</div>

  <section class="offer">
    <div class="offer-title">DISCOUNT UNTIL JULY</div>
    <div class="offer-sub">PAY ONLY HALF PRICE OF THE SERVICE FEE</div>
  </section>

  <section class="services">
    <svg width="753" height="370" style="position:absolute;left:0;top:0" aria-hidden="true">
      <g stroke="#333" stroke-width="1.5">
        <line x1="268" y1="118" x2="268" y2="360"/>
        <line x1="463" y1="118" x2="463" y2="360"/>
        <line x1="92" y1="240" x2="640" y2="240"/>
      </g>
    </svg>
    <div class="service service-lead" style="left:163px;top:6px">
      <svg width="60" height="60" viewBox="0 0 60 60"><circle cx="30" cy="30" r="28.5" fill="#8c8c8c" stroke="#5cc8f0" stroke-width="2"/><g fill="none" stroke="#fff" stroke-width="1.6"><rect x="27" y="13" width="6" height="24" rx="3"/><circle cx="30" cy="41" r="6"/><line x1="36" y1="18" x2="40" y2="18"/><line x1="36" y1="23" x2="40" y2="23"/><line x1="36" y1="28" x2="40" y2="28"/></g></svg>
      Commercial Refrigeration</div>

    <div class="service" style="left:75px;top:128px">
      <svg width="60" height="60" viewBox="0 0 60 60"><circle cx="30" cy="30" r="28.5" fill="#8c8c8c" stroke="#5cc8f0" stroke-width="2"/><g fill="none" stroke="#fff" stroke-width="1.6"><path d="M18 15h24l-3 31H21z"/><rect x="23" y="20" width="7" height="7"/><rect x="30" y="29" width="7" height="7"/></g></svg>
      Ice Makers</div>
    <div class="service" style="left:263px;top:128px">
      <svg width="60" height="60" viewBox="0 0 60 60"><circle cx="30" cy="30" r="28.5" fill="#8c8c8c" stroke="#5cc8f0" stroke-width="2"/><g fill="none" stroke="#fff" stroke-width="1.6"><path d="M22 38V30h12v8h-4M28 30V22l8-9"/><circle cx="32" cy="44" r="2"/></g></svg>
      Beer Systems</div>
    <div class="service" style="left:458px;top:128px">
      <svg width="60" height="60" viewBox="0 0 60 60"><circle cx="30" cy="30" r="28.5" fill="#8c8c8c" stroke="#5cc8f0" stroke-width="2"/><path d="M34 13L22 32h8l-4 15 12-20h-8z" fill="none" stroke="#fff" stroke-width="1.6"/></svg>
      Electrical</div>

    <div class="service" style="left:75px;top:260px">
      <svg width="60" height="60" viewBox="0 0 60 60"><circle cx="30" cy="30" r="28.5" fill="#8c8c8c" stroke="#5cc8f0" stroke-width="2"/><g fill="none" stroke="#fff" stroke-width="1.6"><line x1="18" y1="18" x2="42" y2="42"/><line x1="42" y1="16" x2="18" y2="42"/><circle cx="18" cy="18" r="3"/><circle cx="42" cy="42" r="3"/></g></svg>
      24hr Service</div>
    <div class="service" style="left:263px;top:260px">
      <svg width="60" height="60" viewBox="0 0 60 60"><circle cx="30" cy="30" r="28.5" fill="#8c8c8c" stroke="#5cc8f0" stroke-width="2"/><g fill="none" stroke="#fff" stroke-width="1.6"><path d="M12 18h5l4 18h22l3-13H19"/><circle cx="23" cy="42" r="2.5"/><circle cx="40" cy="42" r="2.5"/></g></svg>
      Sales</div>
    <div class="service" style="left:458px;top:260px">
      <svg width="60" height="60" viewBox="0 0 60 60"><circle cx="30" cy="30" r="28.5" fill="#8c8c8c" stroke="#5cc8f0" stroke-width="2"/><g fill="none" stroke="#fff" stroke-width="1.6"><path d="M18 38l20-20 4 4-20 20-6 2z"/><path d="M20 18l22 22-4 4-22-22z"/></g></svg>
      Installation</div>
  </section>

  <section class="contact">
    <div>PO Box 4418 Bronte NSW 2024</div>
    <div>ABN: 51 702 384 119 &nbsp;|&nbsp; Licence No: 418275D</div>
    <div class="web">WWW.BRISKO-COOLWORKS.COM.AU</div>
  </section>

  <div class="bar bar-phone"><svg width="16" height="14" viewBox="0 0 16 14"><path d="M1 5c0-3 14-3 14 0v2h-4V5H5v2H1zM3 8h10l1 5H2z" fill="#5cc8f0"/></svg>0412 580 734</div>
  <div class="bar bar-mail"><svg width="16" height="12" viewBox="0 0 16 12"><rect x="0.5" y="0.5" width="15" height="11" fill="#000"/><path d="M1 1l7 6 7-6" fill="none" stroke="#5cc8f0"/></svg>info@brisko-coolworks.com.au</div>
  <div class="base"></div>
</main>
</body>
</html>
```